International oil and gas consultancy business needs a web design

Hello, I need a web design for a new oil and gas auditing consultancy business. My business undertakes contract audit assignments to review past costs of oil and gas operations (see attached Excel file for more details of the businesses services). I need the design to give the impression of a professional consultancy style of business, rather than a retail style of website. Note: this job is for LAYOUT DESIGN ONLY and not coding / development work.
The following are my key design principles:
1. BASIC DESIGN: I am after a simple and static web design. I don't want the pages busy or cluttered with too many images or detail.
2. HORIZONTAL TABS: I require a horizontal set of tabs towards the top of the screens (see Excel file) which remain in the same position on every page.
3. META TAG PLANNING: The design should allow for effective positioning of content so that key meta tag words can easily be built during the technical build stage.
4. NUMBER OF PAGES: The site will eventually have a maximum of 10 pages. Seven of the pages will reside under the tabs. Can you please present your opening submission for the first two page.
5. USE OF MY LOGO: The attached logo (JPEG file) should be used throughout the website. Please don't change the shape and colour.
6. COLOUR SCHEMES: Can you please consider any of the 3 colour schemes below:
A - dark red (to match the logo), light grey and perhaps another of your liking;
B - dark red (to match the logo), light cream and perhaps another of your liking;
C - dark red (to match the logo), white and perhaps another of your liking.
7. WORD CONTENT: I have attached an Excel file which shows the estimated word content for each page.
8. FUTURE USE OF DESIGN: I'm planning on building a Wordpress website. Can you please ensure the layout design supports this application.

Target Market(s)

oil and gas companies (small and large)

Industry/Entity Type

Oil And Gas

Font styles to use
Sans Serif

Requirements
Nice to have
• The KRL logo and business name should ideally be next to each other. Also, the logo and name should be part of the background graphics, not above it.

```html
<!DOCTYPE html>
<html lang="en">
<head>
<meta charset="utf-8">
<title>KRL – Keystone Review Labs</title>
<link rel="stylesheet" href="https://fonts.googleapis.com/css2?family=Noto+Serif:wght@400;700&family=Open+Sans:wght@400;600;700&family=Arimo:wght@400&display=swap">
<style>
  :root {
    --brand-red: #93171c;
    --brand-red-dark: #7c1216;
    --ink: #3a3a3a;
    --ink-soft: #6b6b6b;
    --nav-top: #3a3a3a;
    --nav-bottom: #050505;
    --footer-bg: #3d3d3d;
    --footer-text: #ffffff;
    --footer-muted: #e6e6e6;
    --card-border: #e2e2e2;
    --page-bg: #ffffff;
  }
  * { box-sizing: border-box; margin: 0; padding: 0; }
  html, body { width: 1200px; height: 1098px; overflow: hidden; background: var(--page-bg); }
  body { position: relative; font-family: "Open Sans", sans-serif; color: var(--ink); }

  .top-rule { position: absolute; left: 0; top: 0; width: 1200px; height: 4px; background: var(--brand-red); }

  .brand { position: absolute; left: 141px; top: 30px; }
  .brand-name { font-family: "Open Sans", sans-serif; font-weight: 700; font-size: 52px; line-height: 56px; color: var(--brand-red); letter-spacing: 2px; }
  .brand-tagline { font-family: "Open Sans", sans-serif; font-size: 13.5px; color: #222; margin-top: 2px; }

  .search { position: absolute; left: 769px; top: 61px; width: 289px; height: 30px; display: flex; }
  .search-field { flex: 1; border: 1px solid #d6d6d6; border-right: none; border-radius: 3px 0 0 3px; font-size: 12.5px; color: #444; padding: 6px 8px; box-shadow: inset 0 1px 2px rgba(0,0,0,.08); }
  .search-button { width: 32px; background: var(--brand-red); border-radius: 0 3px 3px 0; display: flex; align-items: center; justify-content: center; }

  .main-nav { position: absolute; left: 141px; top: 136px; width: 917px; height: 43px; background: linear-gradient(var(--nav-top), var(--nav-bottom)); border-bottom: 4px solid var(--brand-red); border-radius: 3px 3px 0 0; display: flex; justify-content: space-between; align-items: center; padding: 0 17px; }
  .main-nav a { font-family: "Noto Serif", serif; font-weight: 700; font-size: 13.5px; color: #fff; text-decoration: none; letter-spacing: .2px; }

  .hero { position: absolute; left: 141px; top: 179px; width: 917px; height: 368px; background: linear-gradient(90deg, #e9edf0 0%, #d4dde3 35%, #8fb1cf 55%, #c9a87a 75%, #eef0f0 100%); }
  .hero-dots { position: absolute; left: 424px; top: 331px; display: flex; gap: 11px; }
  .hero-dots span { width: 9px; height: 9px; border-radius: 50%; background: #e8e8e8; box-shadow: 0 0 2px rgba(0,0,0,.3); }
  .hero-dots span.is-active { background: #c8201f; }

  .section-title { position: absolute; left: 0; width: 1200px; text-align: center; font-family: "Noto Serif", serif; font-size: 21px; color: var(--brand-red); }
  .welcome-title { top: 568px; }
  .welcome-text { position: absolute; left: 146px; top: 606px; width: 908px; text-align: center; font-size: 12.8px; line-height: 22.5px; color: #333; }
  .services-title { top: 687px; }

  .service-card { position: absolute; top: 734px; width: 275px; height: 236px; border: 1px solid var(--card-border); box-shadow: 1px 1px 3px rgba(0,0,0,.08); background: #fff; }
  .service-card:nth-of-type(1) { left: 141px; }
  .service-card:nth-of-type(2) { left: 462px; }
  .service-card:nth-of-type(3) { left: 784px; }
  .service-image { position: absolute; left: 14px; top: 14px; width: 247px; height: 107px; }
  .service-name { position: absolute; left: 14px; top: 129px; font-family: "Noto Serif", serif; font-size: 19px; color: var(--brand-red); }
  .service-text { position: absolute; left: 15px; top: 157px; width: 250px; font-size: 11.8px; line-height: 18.7px; color: var(--ink-soft); }
  .learn-more { position: absolute; left: 16px; top: 199px; font-size: 12.5px; font-weight: 700; color: #333; text-decoration: none; }
  .learn-more::after { content: "›"; color: #888; margin-left: 4px; font-size: 15px; }

  .site-footer { position: absolute; left: 0; top: 1009px; width: 1200px; height: 89px; background: var(--footer-bg); }
  .footer-nav { position: absolute; left: 141px; top: 23px; font-family: "Arimo", sans-serif; font-size: 12px; color: var(--footer-text); }
  .footer-nav a { color: var(--footer-text); text-decoration: none; }
  .footer-nav .sep { margin: 0 7px; }
  .copyright { position: absolute; left: 141px; top: 51px; font-size: 12px; color: var(--footer-muted); }
  .social { position: absolute; left: 952px; top: 25px; display: flex; gap: 8px; }
  .social span { width: 30px; height: 30px; border-radius: 50%; }
  .social .fb { background: #3b5a9a; }
  .social .tw { background: #28a9e0; }
  .social .gp { background: #e2442f; }
</style>
</head>
<body>
  <div class="top-rule"></div>

  <header>
    <div class="brand">
      <div class="brand-name">KRL</div>
      <div class="brand-tagline">Keystone Review Labs</div>
    </div>
    <div class="search">
      <div class="search-field">Search</div>
      <div class="search-button">
        <svg width="16" height="16" viewBox="0 0 16 16" aria-hidden="true">
          <circle cx="6" cy="6" r="4" fill="none" stroke="#fff" stroke-width="2"/>
          <line x1="9" y1="9" x2="14" y2="14" stroke="#fff" stroke-width="2.5" stroke-linecap="round"/>
        </svg>
      </div>
    </div>
    <nav class="main-nav">
      <a href="#">HOME</a>
      <a href="#">ABOUT US</a>
      <a href="#">SERVICES</a>
      <a href="#">OUR PARTNERS</a>
      <a href="#">APPROACH</a>
      <a href="#">WHY CHOOSE US</a>
      <a href="#">CONTACT US</a>
    </nav>
  </header>

  <div class="hero" role="img" aria-label="Photo of two colleagues reviewing an audit notebook in a bright office">
    <div class="hero-dots"><span class="is-active"></span><span></span><span></span><span></span></div>
  </div>

  <h1 class="section-title welcome-title">Welcome To Our Company</h1>
  <p class="welcome-text">There are many variations of passages of Lorem Ipsum available, but the majority have suffered alteration in some form, by injected humour, or randomised words which don't look even slightly believable. If you are going to use a passage of Lorem Ipsum, you need to be sure there isn't anything embarrassingeven slightly believable.&nbsp; Ipsum, you&nbsp; hidden in the middle of text.</p>

  <h2 class="section-title services-title">Our Services</h2>

  <article class="service-card">
    <div class="service-image" role="img" aria-label="Photo of hands holding a tablet showing a blue floor plan" style="background: linear-gradient(90deg,#8a6a55,#3aa0e0 45%,#2b2b2b 80%,#9a7a65);"></div>
    <h3 class="service-name">Joint Venture audits</h3>
    <p class="service-text">Lorem Ipsum available, but the majority have suffered alteration in some form</p>
    <a class="learn-more" href="#">Learn More</a>
  </article>
  <article class="service-card">
    <div class="service-image" role="img" aria-label="Photo of a calculator displaying the word audit beside a purple shape" style="background: linear-gradient(90deg,#6a3ae0,#b9a6ee 30%,#d9d9d9 55%,#5a5a5a);"></div>
    <h3 class="service-name">Contract audits</h3>
    <p class="service-text">Lorem Ipsum available, but the majority have suffered alteration in some form</p>
    <a class="learn-more" href="#">Learn More</a>
  </article>
  <article class="service-card">
    <div class="service-image" role="img" aria-label="Photo of a presenter pointing at a diagram on a screen" style="background: linear-gradient(90deg,#e8e6e2,#3a3330 30%,#f2f2f2 55%,#d8dde2);"></div>
    <h3 class="service-name">Operations audits</h3>
    <p class="service-text">Lorem Ipsum available, but the majority have suffered alteration in some form</p>
    <a class="learn-more" href="#">Learn More</a>
  </article>

  <footer class="site-footer">
    <nav class="footer-nav">
      <a href="#">HOME</a><span class="sep">/</span><a href="#">ABOUT US</a><span class="sep">/</span><a href="#">SERVICES</a><span class="sep">/</span><a href="#">OUR PARTNERS</a><span class="sep">/</span><a href="#">APPROACH</a><span class="sep">/</span><a href="#">WHY CHOOSE US</a><span class="sep">/</span><a href="#">CONTACT US</a>
    </nav>
    <p class="copyright">© 2014 KRL All right reserved</p>
    <div class="social">
      <span class="fb" role="img" aria-label="Social network link"></span>
      <span class="tw" role="img" aria-label="Social network link"></span>
      <span class="gp" role="img" aria-label="Social network link"></span>
    </div>
  </footer>
</body>
</html>
```